Website to design and sell sundials: www.gnomonvale.com

We have a website that creates a free paper sundial, we want to migrate from this not profit free website to a website where we will continue offering the free paper sundial model but We will also offer a manufactured sundial and sell it.
In order to understand the project, please visit:
http://www.gnomonvale.com/vertical/sundial.html and
http://www.torvel.net/landing/

The website user journey should be redesigned, including the phases that are,
select language
Show product give info
Creation/edit sundial (could be one or more phases)
View created sundial
Buy sundial.

May some of them could be combined or splitted, what It have more sense.

Requirements
Must have
• A description page user journey offering freemium paper sundial and physical sundial to sell.
• A sundial creation page for "free" paper sundial
• A result page for paper sundial
• A sell page for physical

```html
<!DOCTYPE html>
<html lang="en">
<head>
<meta charset="utf-8">
<title>GnomonVale – Build your customized sundial</title>
<link rel="stylesheet" href="https://fonts.googleapis.com/css2?family=Open+Sans:wght@400;600;700&display=swap">
<style>
  :root {
    --red: #b8100e;
    --red-dark: #9e0b0a;
    --ink: #1f1f1f;
    --text: #333333;
    --muted: #8a8a8a;
    --line: #c9c9c9;
    --panel: #efefef;
    --footer: #1b1b1b;
    --white: #ffffff;
  }
  * { box-sizing: border-box; margin: 0; padding: 0; }
  html, body { width: 1200px; height: 2459px; overflow: hidden; }
  body { font-family: "Open Sans", Arial, sans-serif; color: var(--text); background: var(--white); }
  .page { position: relative; width: 1200px; height: 2459px; }
  section, footer { position: relative; width: 1200px; }
  .abs { position: absolute; }
  .center { left: 0; right: 0; text-align: center; }

  /* Hero */
  .hero { height: 613px; }
  .hero-backdrop { position: absolute; inset: 0; background: linear-gradient(180deg, #ececec 0%, #f4f4f4 45%, #e6e6e6 100%); }
  .brand { left: 133px; top: 34px; display: flex; align-items: center; gap: 12px; }
  .brand-dot { width: 30px; height: 30px; border-radius: 50%; background: var(--red); }
  .brand-name { font-size: 26px; font-weight: 600; color: var(--red); letter-spacing: -0.3px; }
  .lang-select { left: 946px; top: 26px; width: 120px; height: 35px; background: var(--white); border: 1px solid #e0e0e0; display: flex; align-items: center; padding: 0 10px; font-size: 11px; color: #555; gap: 7px; }
  .lang-select .caret { margin-left: auto; }
  .hero-title { top: 165px; font-size: 47px; font-weight: 700; color: var(--ink); letter-spacing: 0.5px; line-height: 1.1; }
  .hero-sub { top: 219px; font-size: 13.5px; color: var(--ink); }
  .hero-product { left: 484px; top: 272px; width: 209px; height: 138px; background: linear-gradient(135deg, #c9b9a0, #a8947a); transform: skewY(-4deg); box-shadow: 0 8px 14px rgba(0,0,0,.25); }
  .btn-order { width: 177px; height: 54px; background: linear-gradient(180deg, #c8160f, var(--red-dark)); color: var(--white); font-size: 19px; display: flex; align-items: center; justify-content: center; gap: 11px; border-radius: 2px; }
  .hero .btn-order { left: 511px; top: 484px; }
  .slider-dots { top: 574px; left: 0; right: 0; display: flex; justify-content: center; gap: 14px; }
  .slider-dots span { width: 9px; height: 9px; border-radius: 50%; border: 1px solid #b5b5b5; background: #f5f5f5; }
  .slider-dots span.active { background: #c6c6c6; }

  /* Intro */
  .intro { height: 235px; }
  .section-heading { font-size: 42px; font-weight: 400; line-height: 1.2; }
  .section-heading.red { color: var(--red); }
  .section-heading.dark { color: var(--ink); }
  .intro .section-heading { top: 42px; }
  .intro-text { left: 131px; width: 938px; top: 102px; font-size: 11px; line-height: 19px; color: var(--muted); text-align: justify; text-align-last: center; }

  /* Needs */
  .needs { height: 380px; background: radial-gradient(ellipse at 20% 20%, #fbfbfb 0%, #ececec 55%, #d9d9d9 100%); }
  .needs .section-heading { top: 32px; }
  .have-row { top: 114px; display: flex; justify-content: center; gap: 40px; font-size: 16px; color: var(--ink); }
  .have-row .item { display: flex; align-items: center; gap: 7px; }
  .have-label { margin-right: -12px; }
  .rule { left: 133px; width: 934px; top: 168px; border-top: 1px solid #cfcfcf; }
  .know-label { top: 195px; font-size: 16px; color: var(--ink); }

  .steps { left: 133px; width: 934px; display: flex; justify-content: space-between; }
  .steps::before { content: ""; position: absolute; left: 100px; right: 100px; top: 15px; border-top: 1px solid var(--line); }
  .step { position: relative; width: 202px; text-align: center; }
  .step-icon { width: 30px; height: 30px; margin: 0 auto; background: transparent; display: flex; align-items: center; justify-content: center; position: relative; z-index: 1; }
  .needs .step-icon { background: #e9e9e9; }
  .instructions .step-icon { background: var(--white); }
  .needs .steps { top: 1086px; top: 238px; }
  .needs .step-text { margin-top: 19px; font-size: 13px; line-height: 18px; color: var(--ink); }

  /* Instructions */
  .instructions { height: 567px; }
  .instructions .section-heading { top: 44px; }
  .instructions .steps { top: 124px; }
  .step-title { margin-top: 13px; font-size: 13px; color: var(--ink); text-transform: uppercase; }
  .step-desc { margin-top: 3px; font-size: 10px; line-height: 16px; color: var(--ink); }
  .step-desc .link { color: var(--red); display: block; }
  .fold-diagram { left: 462px; top: 264px; width: 259px; height: 270px; background: linear-gradient(160deg, #fbfbfb, #f0f0f0); border: 1px solid #eee; }

  /* Gallery */
  .gallery { height: 328px; background: var(--panel); }
  .gallery .section-heading { top: 28px; color: var(--ink); }
  .gallery-grid { left: 133px; top: 108px; display: flex; gap: 31px; }
  .gallery-card { width: 210px; text-align: center; }
  .gallery-photo { width: 210px; height: 143px; background: radial-gradient(ellipse at 50% 45%, #b9c4d8 0%, #9aa8c0 35%, #3d4a1f 62%, #2a3515 100%); }
  .gallery-caption { margin-top: 15px; font-size: 12.5px; color: var(--ink); }

  /* CTA */
  .cta { height: 262px; }
  .cta-title { top: 40px; font-size: 47px; font-weight: 700; color: var(--red); letter-spacing: 0.5px; line-height: 1.1; }
  .cta-sub { top: 95px; font-size: 13.5px; color: var(--ink); }
  .cta .btn-order { left: 511px; top: 134px; }
  .pay-row { top: 209px; display: flex; justify-content: center; gap: 10px; }
  .pay-badge { width: 33px; height: 21px; border: 1px solid #d5d5d5; border-radius: 2px; background: #f6f6f6; }

  /* Footer */
  .site-footer { height: 74px; background: var(--footer); }
  .copyright { left: 133px; top: 28px; font-size: 11.5px; color: #d0d0d0; }
  .social { left: 1006px; top: 22px; display: flex; gap: 6px; }
  .social span { width: 26px; height: 26px; border-radius: 50%; }
  .social .s1 { background: #3b5a9a; }
  .social .s2 { background: #2aa3ef; }
</style>
</head>
<body>
<div class="page">

  <section class="hero">
    <div class="hero-backdrop" role="img" aria-label="White painted brick wall background"></div>
    <div class="abs brand">
      <span class="brand-dot"></span>
      <span class="brand-name">GnomonVale.com</span>
    </div>
    <div class="abs lang-select">
      <svg width="10" height="10" viewBox="0 0 10 10"><circle cx="5" cy="5" r="4.3" fill="none" stroke="#555" stroke-width="1.2"/><path d="M1 5h8M5 1c-2 2.5-2 5.5 0 8M5 1c2 2.5 2 5.5 0 8" fill="none" stroke="#555" stroke-width=".8"/></svg>
      <span>English</span>
      <svg class="caret" width="8" height="5" viewBox="0 0 8 5"><path d="M1 1l3 3 3-3" fill="none" stroke="#777" stroke-width="1.2"/></svg>
    </div>
    <h1 class="abs center hero-title">BUILD YOUR CUSTOMIZED SUNDIAL</h1>
    <p class="abs center hero-sub">We can manufacture your Sundial, design to your specific location. Becoming a unique piece considering your location, and wall decliantion.</p>
    <div class="abs hero-product" role="img" aria-label="Folded paper vertical sundial with hour lines"></div>
    <a class="abs btn-order">
      <svg width="16" height="14" viewBox="0 0 16 14"><path d="M0 1h3l2 8h8l2-6H4" fill="none" stroke="#fff" stroke-width="1.8"/><circle cx="6" cy="12" r="1.4" fill="#fff"/><circle cx="12" cy="12" r="1.4" fill="#fff"/></svg>
      Order Now
    </a>
    <div class="abs slider-dots"><span class="active"></span><span></span><span></span><span></span></div>
  </section>

  <section class="intro">
    <h2 class="abs center section-heading red">Introduction</h2>
    <p class="abs intro-text">Sundials are instruments that tell you the time with the shadow of the sun. To design a sundial you need to know exactly where you are going to put it, i.e. you need to know the longitude, the latitude and the orientation of the wall with respect to North. I have designed this page and integrated Terramap. It helps you to easily find all the parameters needed and finally produces a printable page with a cut-out paper sundial, that can be cut and folded to give you a vertical sundial. This page allows you to make your own Cut Out Paper Vertical Sundial customized to your place on earth and the declination of the wall you are going to put it on.</p>
  </section>

  <section class="needs">
    <h2 class="abs center section-heading dark">What you need</h2>
    <div class="abs center have-row">
      <span class="have-label">You need to have :</span>
      <span class="item"><svg width="11" height="13" viewBox="0 0 11 13"><path d="M1 1h6l3 3v8H1z" fill="none" stroke="#222" stroke-width="1.2"/><path d="M3 6h5M3 8h5M3 10h5" stroke="#222"/></svg>This webpage</span>
      <span class="item"><svg width="13" height="12" viewBox="0 0 13 12"><rect x="3" y="0" width="7" height="4" fill="#222"/><rect x="0" y="4" width="13" height="5" rx="1" fill="#222"/><rect x="3" y="8" width="7" height="4" fill="#fff" stroke="#222"/></svg>A printer</span>
      <span class="item"><svg width="13" height="12" viewBox="0 0 13 12"><circle cx="3" cy="3" r="2" fill="none" stroke="#222" stroke-width="1.2"/><circle cx="3" cy="9" r="2" fill="none" stroke="#222" stroke-width="1.2"/><path d="M4.5 4L12 9.5M4.5 8L12 2.5" stroke="#222" stroke-width="1.2"/></svg>Scissors</span>
    </div>
    <div class="abs rule"></div>
    <p class="abs center know-label">You need to know</p>
    <div class="abs steps">
      <div class="step">
        <div class="step-icon"><svg width="18" height="24" viewBox="0 0 18 24"><path d="M9 1a8 8 0 0 0-8 8c0 6 8 14 8 14s8-8 8-14a8 8 0 0 0-8-8z" fill="#333"/><circle cx="9" cy="9" r="3" fill="#e9e9e9"/></svg></div>
        <p class="step-text">Where is the wall where you want to put your sundial on, located it with the map.</p>
      </div>
      <div class="step">
        <div class="step-icon"><svg width="24" height="24" viewBox="0 0 24 24"><circle cx="12" cy="12" r="10" fill="none" stroke="#333" stroke-width="2.4"/><path d="M16 8l-2.5 5.5L8 16l2.5-5.5z" fill="#333"/></svg></div>
        <p class="step-text">Select the N/S/E/W face desired, from the pull-down menu.</p>
      </div>
      <div class="step">
        <div class="step-icon"><svg width="24" height="24" viewBox="0 0 24 24"><circle cx="12" cy="12" r="10" fill="none" stroke="#333" stroke-width="2.4"/><path d="M12 6v6h4" fill="none" stroke="#333" stroke-width="2.2"/></svg></div>
        <p class="step-text">Select your timezone or true local time for solar time</p>
      </div>
      <div class="step">
        <div class="step-icon"><svg width="26" height="26" viewBox="0 0 26 26"><g stroke="#333" stroke-width="3"><path d="M13 1v5M13 20v5M1 13h5M20 13h5M4.5 4.5l3.5 3.5M18 18l3.5 3.5M4.5 21.5L8 18M18 8l3.5-3.5"/></g><circle cx="13" cy="13" r="7" fill="none" stroke="#333" stroke-width="2.4"/></svg></div>
        <p class="step-text">Select if you are Daylight saving time</p>
      </div>
    </div>
  </section>

  <section class="instructions">
    <h2 class="abs center section-heading red">Instructions</h2>
    <div class="abs steps">
      <div class="step">
        <div class="step-icon"><svg width="20" height="22" viewBox="0 0 20 22"><rect x="1" y="1" width="18" height="20" fill="none" stroke="#333" stroke-width="1.8"/><rect x="4" y="4" width="12" height="4" fill="#333"/><g fill="#333"><rect x="4" y="10" width="3" height="2"/><rect x="8.5" y="10" width="3" height="2"/><rect x="13" y="10" width="3" height="2"/><rect x="4" y="14" width="3" height="2"/><rect x="8.5" y="14" width="3" height="2"/><rect x="13" y="14" width="3" height="2"/></g></svg></div>
        <p class="step-title">Calculate</p>
        <p class="step-desc"><span class="link">Click here to build your custom sundial!!!</span>Fill in the form and create your sundial</p>
      </div>
      <div class="step">
        <div class="step-icon"><svg width="18" height="22" viewBox="0 0 18 22"><path d="M1 1h11l5 5v15H1z" fill="none" stroke="#333" stroke-width="1.8"/><path d="M12 1v5h5" fill="none" stroke="#333" stroke-width="1.5"/><path d="M5 16c3-1 5-4 5-8 1 4 2 6 4 7-3 0-6 0-9 1z" fill="none" stroke="#333" stroke-width="1.2"/></svg></div>
        <p class="step-title">Print the PDF</p>
        <p class="step-desc">To print, please select "shrink to page" in order not to deform the shape of the page.</p>
      </div>
      <div class="step">
        <div class="step-icon"><svg width="24" height="20" viewBox="0 0 24 20"><circle cx="5" cy="5" r="3.5" fill="none" stroke="#333" stroke-width="2"/><circle cx="5" cy="15" r="3.5" fill="none" stroke="#333" stroke-width="2"/><path d="M8 7l15 10M8 13L23 3" stroke="#333" stroke-width="2"/></svg></div>
        <p class="step-title">Cut and fold</p>
        <p class="step-desc">Once you have your model printed, you have to cut (RED LINES), and fold (BLUE LINES)</p>
      </div>
      <div class="step">
        <div class="step-icon"><svg width="22" height="22" viewBox="0 0 22 22"><circle cx="11" cy="11" r="9.5" fill="none" stroke="#333" stroke-width="2.2"/><path d="M6.5 11l3.2 3.2L15.5 8" fill="none" stroke="#333" stroke-width="2.4"/></svg></div>
        <p class="step-title">Put on your wall</p>
        <p class="step-desc">Put on your wall or Window.</p>
      </div>
    </div>
    <div class="abs fold-diagram" role="img" aria-label="Cut-out paper sundial template with red cut lines, blue fold lines and hour markings"></div>
  </section>

  <section class="gallery">
    <h2 class="abs center section-heading">View created sundial</h2>
    <div class="abs gallery-grid">
      <div class="gallery-card">
        <div class="gallery-photo" role="img" aria-label="Finished metal sundial lying on grass"></div>
        <p class="gallery-caption">South Hemisphere Buenos Aires</p>
      </div>
      <div class="gallery-card">
        <div class="gallery-photo" role="img" aria-label="Finished metal sundial lying on grass"></div>
        <p class="gallery-caption">Valencia South east</p>
      </div>
      <div class="gallery-card">
        <div class="gallery-photo" role="img" aria-label="Finished metal sundial lying on grass"></div>
        <p class="gallery-caption">Valencia NORTH WEST</p>
      </div>
      <div class="gallery-card">
        <div class="gallery-photo" role="img" aria-label="Finished metal sundial lying on grass"></div>
        <p class="gallery-caption">Valencia WEST</p>
      </div>
    </div>
  </section>

  <section class="cta">
    <h2 class="abs center cta-title">BUILD YOUR CUSTOMIZED SUNDIAL</h2>
    <p class="abs center cta-sub">We can manufacture your Sundial, design to your specific location. Becoming a unique piece considering your location, and wall decliantion.</p>
    <a class="abs btn-order">
      <svg width="16" height="14" viewBox="0 0 16 14"><path d="M0 1h3l2 8h8l2-6H4" fill="none" stroke="#fff" stroke-width="1.8"/><circle cx="6" cy="12" r="1.4" fill="#fff"/><circle cx="12" cy="12" r="1.4" fill="#fff"/></svg>
      Order Now
    </a>
    <div class="abs pay-row">
      <span class="pay-badge"></span><span class="pay-badge"></span><span class="pay-badge"></span><span class="pay-badge"></span>
    </div>
  </section>

  <footer class="site-footer">
    <p class="abs copyright">Copyright &nbsp;©&nbsp; 2016 &nbsp;GnomonVale. &nbsp; All rights reserved.</p>
    <div class="abs social"><span class="s1"></span><span class="s2"></span></div>
  </footer>

</div>
</body>
</html>
```